Woman owned consulting company needs an elegant and modern business card design

I need a business card design for my new consulting company, Mara Quillon Consulting. I am looking for something that is simple and elegant, but also creative and original. You can use either version of the logo that are attached. I have also included the information that needs to be featured on the business card.

Contact Information for Business Card

Requirements
Must have
• The logo and the font type and a standard business card size. Use shades of gray/silver and or rose gold that are in the logo.
• I didn't realize that my actual logo wasn't attached. Please incorporate in the designs.
Should not have
• Colors that are different from my logo

```html
<!DOCTYPE html>
<html lang="en">
<head>
<meta charset="utf-8">
<title>Mara Quillon Consulting — Business Card</title>
<link rel="stylesheet" href="https://fonts.googleapis.com/css2?family=Cinzel:wght@400;600&family=Libre+Baskerville:wght@400;700&display=swap">
<style>
  :root {
    --backdrop: #bdbdbd;
    --card: #f7f7f7;
    --silver: #9a9a9a;
    --silver-light: #b3b3b3;
    --ink: #1f1f1f;
    --ink-soft: #444444;
    --edge: #3b3f44;
  }
  * { box-sizing: border-box; margin: 0; padding: 0; }
  html, body {
    width: 1200px; height: 852px; overflow: hidden;
    background: var(--backdrop);
  }
  .stage {
    position: relative; width: 1200px; height: 852px;
    display: flex; align-items: center; justify-content: center; gap: 44px;
  }
  .card {
    position: relative; width: 490px; height: 280px;
    background: var(--card); border-radius: 16px;
    box-shadow: 0 6px 18px rgba(0,0,0,0.18);
    overflow: hidden;
  }
  /* Front: brand side */
  .card--front {
    display: flex; flex-direction: column; align-items: center; justify-content: center;
    border-bottom: 8px solid var(--edge);
  }
  .brand-lockup {
    display: flex; align-items: center; gap: 16px; margin-top: 6px;
  }
  .brand-dot {
    width: 14px; height: 14px; border-radius: 50%;
    background: var(--silver-light);
  }
  .brand-name {
    font-family: "Cinzel", serif; font-weight: 400;
    color: var(--silver); font-size: 27px; line-height: 1.15;
    letter-spacing: 1px;
  }
  .brand-name span { display: block; }
  .front-web {
    margin-top: 44px;
    font-family: "Libre Baskerville", serif; font-size: 11px;
    color: var(--ink-soft); letter-spacing: 0.3px;
  }
  /* Back: contact side */
  .card--back { display: flex; align-items: center; padding: 0 30px 0 34px; }
  .back-brand {
    flex: 0 0 200px;
    font-family: "Cinzel", serif; font-weight: 400;
    color: var(--silver); font-size: 30px; line-height: 1.1;
    margin-top: 50px;
  }
  .contact { flex: 1; padding-left: 18px; margin-top: -54px; }
  .contact-name {
    font-family: "Libre Baskerville", serif; font-weight: 700;
    font-size: 17px; letter-spacing: 1px; color: var(--ink);
  }
  .contact-role {
    font-family: "Libre Baskerville", serif; font-size: 10px;
    color: var(--ink-soft); margin: 3px 0 14px;
  }
  .contact-list { list-style: none; }
  .contact-list li {
    display: flex; align-items: center; gap: 8px;
    font-family: "Libre Baskerville", serif; font-size: 10.5px;
    color: var(--ink-soft); line-height: 1.7;
  }
  .contact-list svg { width: 10px; height: 10px; fill: var(--ink); flex: none; }
</style>
</head>
<body>
<main class="stage">
  <section class="card card--front" aria-label="Business card front">
    <div class="brand-lockup">
      <div class="brand-dot"></div>
      <div class="brand-name"><span>Mara Quillon</span><span>Consulting, LLC</span></div>
    </div>
    <p class="front-web">www.maraquillonconsulting.com</p>
  </section>

  <section class="card card--back" aria-label="Business card back">
    <div class="back-brand">Mara Quillon Consulting</div>
    <div class="contact">
      <h1 class="contact-name">MARA QUILLON</h1>
      <p class="contact-role">Owner</p>
      <ul class="contact-list">
        <li>
          <svg viewBox="0 0 24 24" aria-hidden="true"><path d="M6.6 10.8a15.1 15.1 0 0 0 6.6 6.6l2.2-2.2a1 1 0 0 1 1-.25 11.4 11.4 0 0 0 3.6.57 1 1 0 0 1 1 1V20a1 1 0 0 1-1 1A17 17 0 0 1 3 4a1 1 0 0 1 1-1h3.5a1 1 0 0 1 1 1c0 1.25.2 2.45.57 3.57a1 1 0 0 1-.25 1z"/></svg>
          610-555-0147
        </li>
        <li>
          <svg viewBox="0 0 24 24" aria-hidden="true"><path d="M2 5h20v14H2z M3.5 6.5 12 13l8.5-6.5" fill="none" stroke="#1f1f1f" stroke-width="2.4"/></svg>
          mara@maraquillonconsulting.com
        </li>
        <li>
          <svg viewBox="0 0 24 24" aria-hidden="true"><circle cx="12" cy="12" r="10"/><path d="M2 12h20M12 2c3 3 3 17 0 20M12 2c-3 3-3 17 0 20" fill="none" stroke="#f7f7f7" stroke-width="1.5"/></svg>
          www.maraquillonconsulting.com
        </li>
      </ul>
    </div>
  </section>
</main>
</body>
</html>
```